I will ask the design of the business card

We are looking for business card design of the new company "R DOVE PAYGRID WORKS LLC." Based in Azerbaijan.
In case
We are working on Azerbaijan to set up the first exchange of crypto currencies.

The key currency used in exchanges is called "PLUME".
In case
We are doing project to make crypto currency infrastructure.

We provide state-of-the-art technology to the world.

```html
<!DOCTYPE html>
<html lang="en">
<head>
<meta charset="utf-8">
<title>R Dove Paygrid Works LLC – Business Card</title>
<link href="https://fonts.googleapis.com/css2?family=Bebas+Neue&family=Source+Sans+3:wght@400;600&display=swap" rel="stylesheet">
<style>
  :root {
    --page-bg: #2a2a2b;
    --card-bg: #1d1d1e;
    --brand-blue: #1d6aa6;
    --text-light: #e6e6e6;
    --text-muted: #cfcfcf;
    --rule: #8a8a8a;
  }
  * { margin: 0; padding: 0; box-sizing: border-box; }
  html, body {
    width: 1200px; height: 900px; overflow: hidden;
    background: var(--page-bg);
    font-family: "Source Sans 3", "Myriad Pro", sans-serif;
  }
  .sheet {
    width: 1200px; height: 900px;
    display: flex; flex-direction: column; align-items: center; justify-content: center;
    gap: 56px;
  }
  .card {
    position: relative;
    width: 640px; height: 366px;
    background: var(--card-bg);
    border-radius: 22px;
    box-shadow: 0 10px 30px rgba(0,0,0,0.45);
    color: var(--text-light);
  }
  .company-name {
    font-family: "Bebas Neue", "Oswald", sans-serif;
    color: var(--brand-blue);
    font-weight: 400;
    letter-spacing: 0.5px;
    white-space: nowrap;
  }
  /* Front */
  .card--front .company-name {
    position: absolute; right: 48px; top: 112px;
    font-size: 60px; line-height: 1;
  }
  .card--front .rule {
    position: absolute; left: 48px; right: 48px; top: 196px;
    height: 1px; background: var(--rule);
  }
  .card--front .website {
    position: absolute; right: 48px; top: 214px;
    font-size: 15px; letter-spacing: 4px; color: var(--text-light);
  }
  /* Back */
  .card--back .company-name {
    position: absolute; right: 44px; top: 46px;
    font-size: 60px; line-height: 1;
  }
  .card--back .address {
    position: absolute; right: 44px; top: 128px;
    text-align: right; font-size: 15px; line-height: 1.3; color: var(--text-light);
  }
  .card--back .rule {
    position: absolute; left: 40px; right: 40px; top: 184px;
    height: 1px; background: var(--rule);
  }
  .person { position: absolute; left: 40px; top: 198px; }
  .person-name {
    font-family: "Bebas Neue", "Oswald", sans-serif;
    color: var(--brand-blue); font-size: 26px; line-height: 1; letter-spacing: 0.3px;
  }
  .person-role { font-size: 15px; color: var(--text-muted); margin-top: 2px; }
  .person .rule-short {
    width: 210px; height: 1px; background: var(--rule); margin: 10px 0 10px;
  }
  .contact-list { list-style: none; }
  .contact-list li {
    display: flex; align-items: center; gap: 8px;
    font-size: 15px; line-height: 21px; color: var(--text-light);
  }
  .contact-list svg { width: 13px; height: 13px; fill: var(--brand-blue); flex: none; }
</style>
</head>
<body>
<main class="sheet">
  <section class="card card--front" aria-label="Business card front">
    <h1 class="company-name">R DOVE PAYGRID WORKS LLC</h1>
    <div class="rule"></div>
    <p class="website">www.dovepaygrid.az</p>
  </section>

  <section class="card card--back" aria-label="Business card back">
    <h2 class="company-name">R DOVE PAYGRID WORKS LLC</h2>
    <p class="address">48 Nizami Street, Baku<br>Azerbaijan, AZ1000</p>
    <div class="rule"></div>
    <div class="person">
      <p class="person-name">DANIEL HARPER</p>
      <p class="person-role">Managing Director</p>
      <div class="rule-short"></div>
      <ul class="contact-list">
        <li>
          <svg viewBox="0 0 16 16" aria-hidden="true"><path d="M1 5c0-2 3-3 7-3s7 1 7 3v1.5h-3.5V5H4.5v1.5H1zM3 8h10l1.5 6h-13zM8 9.5a2 2 0 1 0 0 4 2 2 0 0 0 0-4z"/></svg>
          055-210 384 617
        </li>
        <li>
          <svg viewBox="0 0 16 16" aria-hidden="true"><path d="M4.5 1h7a1 1 0 0 1 1 1v12a1 1 0 0 1-1 1h-7a1 1 0 0 1-1-1V2a1 1 0 0 1 1-1zm.8 2v9h5.4V3zM8 12.6a.8.8 0 1 0 0 1.6.8.8 0 0 0 0-1.6z"/></svg>
          050-742 196 350
        </li>
        <li>
          <svg viewBox="0 0 16 16" aria-hidden="true"><path d="M1 3h14v1L8 9 1 4zM1 5.5l7 5 7-5V13H1z"/></svg>
          info@dovepaygrid.az
        </li>
      </ul>
    </div>
  </section>
</main>
</body>
</html>
```